Etiketten für Honig
Wir können nur volle Punktzahl geben. Roswitha ist selbst Ideenreich, wirklich nett und setzte unsere Ideen schnell und engagiert um. Hat echt Spass gemacht mit ihr zu arbeiten.
Zielgruppe
Es scheint Missverständnisse zu geben weshalb ich das Briefing wohl ändern muss.
see below for English translation
Wir sind eine kleine Imkerei, die von der Liebhaberei in den Nebenerwerb wechselt. Wir verkaufen verschiedene Sortenhonige und Honigzubereitungen (siehe Webseite) im vorwiegend ländlichen Raum des Münsterlandes.
Entsprechend unseres Standortes und unserer Kundschaft benötigen wir ein klassisch ländliches Design. Hierfür haben wir auch bereits ein Logo welches verwendet werden muss.
English
There seems to be some misunderstanding, so I guess I'll have to change the briefing.
We are a small apiary that changes from hobby to sideline. We sell different types of honey and honey preparations (e.g. honey with raspberry) in a predominantly rural area of the Münsterland (Muensterland).
According to our location and our clientele, we need a classic rural design. We already have a logo which must be used.
Aufgabenstellung
Wir möchten ein rechteckiges Etikett mit Gewährverschluss das für verschiedene Sorten adoptierbar ist. Zum Beispiel durch den Austausch der Sortenbezeichnung und eine farbliche Veränderung.
Das Design soll später auf Naturpapier oder Graspapier gedruckt werden. Das Logo muss auf Etikett und Gewährverschluss abgebildet werden.
We would like a rectangular label with a guarantee seal that is adoptable for different varieties. For example, by exchanging the variety designation and changing the color.
The design will later be printed on uncoated paper or grass paper. The logo must be shown on the label and guarantee seal.

```html
<!DOCTYPE html>
<html lang="de">
<head>
<meta charset="utf-8">
<title>Kreuzfelder Landhonig – Etiketten</title>
<link rel="stylesheet" href="https://fonts.googleapis.com/css2?family=Roboto:wght@400;700&family=Montserrat:wght@500;600&display=swap">
<style>
  :root{
    --kraft:#d9c6a3;
    --kraft-light:#e6d8bd;
    --kraft-dark:#c8b28b;
    --ink:#1d1a16;
    --name-grey:#5b5650;
    --leaf:#7bb843;
    --sun:#f5bd1f;
    --c-fruehtracht:#f5bd1f;
    --c-sommertracht:#f5a02a;
    --c-bluete:#df8fb0;
    --c-akazie:#ad97cc;
    --c-wald:#3d9338;
    --c-kastanie:#a5bb2a;
    --c-raps:#d3d921;
    --panel:#e9e9ea;
  }
  *{box-sizing:border-box;margin:0;padding:0}
  html,body{width:1200px;height:751px;overflow:hidden;background:#fff}
  body{position:relative;font-family:"Roboto",Arial,sans-serif;color:var(--ink)}

  .backdrop{position:absolute;left:76px;top:142px;width:302px;height:309px;background:var(--panel)}

  .kraft{background:radial-gradient(ellipse at 50% 60%,var(--kraft-light) 0%,var(--kraft) 60%,var(--kraft-dark) 100%)}

  .label{position:absolute;width:256px;height:170px;overflow:hidden}
  .label__title{position:absolute;top:24px;left:0;right:0;text-align:center;font-weight:700;font-size:12.5px;letter-spacing:.2px}
  .label__tagline{position:absolute;left:20px;top:68px;width:64px;height:22px;border-radius:3px;background:linear-gradient(90deg,rgba(60,50,40,.25),rgba(60,50,40,.12))}
  .label__mark{position:absolute;left:50%;top:53px;width:46px;height:46px;margin-left:-23px;border-radius:50%;border:3px solid var(--leaf);background:var(--sun)}
  .label__maker{position:absolute;top:102px;left:0;right:0;text-align:center;font-family:"Montserrat",Arial,sans-serif;font-weight:600;font-size:7.5px;letter-spacing:1px;color:var(--name-grey)}
  .label__name{position:absolute;top:107px;left:0;right:0;text-align:center;font-family:"Montserrat",Arial,sans-serif;font-weight:600;font-size:27px;color:var(--name-grey)}
  .label__band{position:absolute;left:0;right:0;bottom:14px;height:13px;background:var(--accent);color:rgba(255,255,255,.85);font-size:7.5px;font-weight:700;letter-spacing:.8px;text-align:center;line-height:13px;text-transform:uppercase}

  .tab{position:absolute;width:51px;height:66px}
  .tab__color{height:24px;background:var(--accent)}
  .tab__text{height:42px;display:flex;align-items:center;justify-content:center;text-align:center;font-size:6px;line-height:1.3;text-transform:uppercase}

  /* unfolded first label */
  .flat{position:absolute;left:33px;top:246px;width:433px;height:150px;overflow:hidden}
  .flat .label{left:67px;top:-16px;height:166px;background:transparent}
  .flat__band{position:absolute;left:0;right:112px;bottom:0;height:13px;background:var(--accent);color:rgba(255,255,255,.8);font-size:7.5px;font-weight:700;letter-spacing:.8px;text-align:center;line-height:13px;text-transform:uppercase}
  .flat__back{position:absolute;right:0;top:0;width:112px;height:100%;padding:7px 6px 0 8px;font-size:6px;line-height:1.35}
  .flat__back p{margin-bottom:6px}
  .flat__rule{border-top:1px solid var(--ink);margin:2px 0 4px}
  .flat__date{width:68px;height:11px;background:#fff;margin-top:2px}
  .flat__weight{position:absolute;left:12px;top:108px;font-size:12px}

  .seal{position:absolute;left:167px;top:16px;width:120px;height:120px;border-radius:50%;background:var(--accent);display:flex;align-items:center;justify-content:center}
  .seal__inner{width:90px;height:90px;border-radius:50%;display:flex;align-items:center;justify-content:center;font-family:"Montserrat",Arial,sans-serif;font-weight:600;font-size:14px;color:var(--name-grey)}
  .seal__strap{position:absolute;left:202px;top:128px;width:50px;height:36px;background:var(--accent)}

  .swatch{position:absolute;left:1071px;width:108px;height:19px}
</style>
</head>
<body>

<div class="backdrop"></div>

<!-- Frühtracht: label with seal, unfolded -->
<div class="seal" style="--accent:var(--c-fruehtracht)">
  <div class="seal__inner kraft">Brenkamp</div>
</div>
<div class="seal__strap" style="--accent:var(--c-fruehtracht)"></div>
<div class="tab kraft" style="left:202px;top:158px;--accent:var(--c-fruehtracht)">
  <div class="tab__text" style="height:66px">Deutscher<br>Honig</div>
</div>
<div class="flat kraft" style="--accent:var(--c-fruehtracht)">
  <div class="label">
    <div class="label__title">KREUZFELDER LANDHONIG</div>
    <div class="label__tagline" role="img" aria-label="Handschriftzug: von Bienen aus dem Münsterland"></div>
    <div class="label__mark"></div>
    <div class="label__maker">HONIGHOF</div>
    <div class="label__name">Brenkamp</div>
  </div>
  <div class="flat__band">Frühtracht</div>
  <div class="flat__back">
    <p>Trocken, Dunkel und vor Wärme geschützt lagern</p>
    <p>Honighof Brenkamp<br>Strassenname 15<br>D-22665 Ortschaft<br>honighof-brenkamp.de</p>
    <p style="margin-bottom:2px">Mehrwegglas bitte an Imkerei zurückgeben</p>
    <div class="flat__rule"></div>
    <div>Mindestens haltbar bis:</div>
    <div class="flat__date"></div>
    <div class="flat__weight">500g</div>
  </div>
</div>

<!-- Sommertracht -->
<div class="tab kraft" style="left:590px;top:160px;--accent:var(--c-sommertracht)"><div class="tab__color"></div><div class="tab__text">Deutscher<br>Honig</div></div>
<div class="label kraft" style="left:488px;top:227px;--accent:var(--c-sommertracht)">
  <div class="label__title">KREUZFELDER LANDHONIG</div>
  <div class="label__tagline" role="img" aria-label="Handschriftzug: von Bienen aus dem Münsterland"></div>
  <div class="label__mark"></div>
  <div class="label__maker">HONIGHOF</div>
  <div class="label__name">Brenkamp</div>
  <div class="label__band">Sommertracht</div>
</div>

<!-- Blütenhonig -->
<div class="tab kraft" style="left:874px;top:160px;--accent:var(--c-bluete)"><div class="tab__color"></div><div class="tab__text">Deutscher<br>Honig</div></div>
<div class="label kraft" style="left:772px;top:227px;--accent:var(--c-bluete)">
  <div class="label__title">KREUZFELDER LANDHONIG</div>
  <div class="label__tagline" role="img" aria-label="Handschriftzug: von Bienen aus dem Münsterland"></div>
  <div class="label__mark"></div>
  <div class="label__maker">HONIGHOF</div>
  <div class="label__name">Brenkamp</div>
  <div class="label__band">Blütenhonig</div>
</div>

<!-- Akazienhonig -->
<div class="tab kraft" style="left:198px;top:456px;--accent:var(--c-akazie)"><div class="tab__color"></div><div class="tab__text">Deutscher<br>Honig</div></div>
<div class="label kraft" style="left:96px;top:522px;--accent:var(--c-akazie)">
  <div class="label__title">KREUZFELDER LANDHONIG</div>
  <div class="label__tagline" role="img" aria-label="Handschriftzug: von Bienen aus dem Münsterland"></div>
  <div class="label__mark"></div>
  <div class="label__maker">HONIGHOF</div>
  <div class="label__name">Brenkamp</div>
  <div class="label__band">Akazienhonig</div>
</div>

<!-- Waldhonig -->
<div class="tab kraft" style="left:480px;top:456px;--accent:var(--c-wald)"><div class="tab__color"></div><div class="tab__text">Deutscher<br>Honig</div></div>
<div class="label kraft" style="left:378px;top:522px;--accent:var(--c-wald)">
  <div class="label__title">KREUZFELDER LANDHONIG</div>
  <div class="label__tagline" role="img" aria-label="Handschriftzug: von Bienen aus dem Münsterland"></div>
  <div class="label__mark"></div>
  <div class="label__maker">HONIGHOF</div>
  <div class="label__name">Brenkamp</div>
  <div class="label__band">Waldhonig</div>
</div>

<!-- Edelkastanie mit Linde -->
<div class="tab kraft" style="left:756px;top:456px;--accent:var(--c-kastanie)"><div class="tab__color"></div><div class="tab__text">Deutscher<br>Honig</div></div>
<div class="label kraft" style="left:654px;top:522px;--accent:var(--c-kastanie)">
  <div class="label__title">KREUZFELDER LANDHONIG</div>
  <div class="label__tagline" role="img" aria-label="Handschriftzug: von Bienen aus dem Münsterland"></div>
  <div class="label__mark"></div>
  <div class="label__maker">HONIGHOF</div>
  <div class="label__name">Brenkamp</div>
  <div class="label__band">Edelkastanie mit Linde</div>
</div>

<!-- Raps -->
<div class="tab kraft" style="left:1039px;top:456px;--accent:var(--c-raps)"><div class="tab__color"></div><div class="tab__text">Deutscher<br>Honig</div></div>
<div class="label kraft" style="left:937px;top:522px;--accent:var(--c-raps)">
  <div class="label__title">KREUZFELDER LANDHONIG</div>
  <div class="label__tagline" role="img" aria-label="Handschriftzug: von Bienen aus dem Münsterland"></div>
  <div class="label__mark"></div>
  <div class="label__maker">HONIGHOF</div>
  <div class="label__name">Brenkamp</div>
  <div class="label__band">Raps</div>
</div>

<!-- colour palette -->
<div class="swatch" style="top:226px;background:var(--c-fruehtracht)"></div>
<div class="swatch" style="top:256px;background:var(--c-sommertracht)"></div>
<div class="swatch" style="top:282px;background:var(--c-bluete)"></div>
<div class="swatch" style="top:308px;background:var(--c-akazie)"></div>
<div class="swatch" style="top:334px;background:var(--c-wald)"></div>
<div class="swatch" style="top:361px;background:var(--c-kastanie)"></div>
<div class="swatch" style="top:387px;background:var(--c-raps)"></div>

</body>
</html>
```